Brindle Sky Port needs a new upscale business card design for our high end aircraft hangar complex

Brindle Sky Port (BSP) is a large, upscale jet hangar complex in the US housing expensive aircraft. We need a new business card design, using our current logo. We will be attending a industry convention and need a card design that will stand out and be remembered by aircraft owners and private pilots.

Target Market(s)

Aircraft pilots or owners looking for a new upscale hangar

Industry/Entity Type

Airport

Contact Information for Business Card

I like to use very heavy card stock, 400#, double sided. Square, no rounded edges please.

Colors
3276b5
0255a3
85abd2

Requirements
Must have
• An expensive, classy design, vivid colors.
Nice to have
• Needs to look very expensive and classy, and have some "pop". Designer must be able to download or copy my current typeface or fonts.
• One card side might be black with the "Logo and Brindle Sky Port Double line image in blue (or try gold, or glossy black), and perhaps have a grayed out "K720 jet silhouette". The other card side would have our contact info, and perhaps the "BSP Logo only". I'd like my contact info 'stacked', not in a paragraph format.
Should not have
• Should not look "too busy". Having a double-sided card will help.

```html
<!DOCTYPE html>
<html lang="en">
<head>
<meta charset="utf-8">
<title>Brindle Sky Port — Business Card</title>
<link href="https://fonts.googleapis.com/css2?family=Roboto:wght@400;500;700&display=swap" rel="stylesheet">
<style>
  :root {
    --backdrop: #a3a3a3;
    --card: #0e0e0e;
    --brand-blue: #3270ad;
    --brand-deep: #0255a3;
    --brand-light: #85abd2;
    --ink: #dcdcdc;
    --ink-soft: #bdbdbd;
    --rule: #2b4f78;
  }
  * { margin: 0; padding: 0; box-sizing: border-box; }
  html, body {
    width: 1105px; height: 1200px; overflow: hidden;
    background: var(--backdrop);
    font-family: "Roboto", Arial, sans-serif;
  }
  .canvas { position: relative; width: 1105px; height: 1200px; }
  .card {
    position: absolute; left: 182px; width: 746px; height: 425px;
    background: var(--card);
  }
  .card--front { top: 119px; }
  .card--back { top: 637px; }

  .brand-name {
    position: absolute; color: var(--brand-blue);
    font-weight: 700; text-transform: uppercase; letter-spacing: 1px;
    text-align: center; line-height: 1.05;
  }
  .card--front .brand-name { left: 440px; top: 94px; width: 280px; font-size: 38px; }
  .card--back .brand-name { left: 223px; top: 168px; width: 300px; font-size: 42px; }

  .holder { position: absolute; left: 39px; top: 188px; }
  .holder-name { color: var(--brand-blue); font-size: 25px; font-weight: 500; }
  .holder-title { color: var(--ink); font-size: 19px; margin-top: 4px; }

  .contact-list { position: absolute; left: 39px; top: 266px; width: 212px; list-style: none; }
  .contact-item {
    display: flex; align-items: center; height: 29px;
    color: var(--ink); font-size: 18.5px; white-space: nowrap;
  }
  .contact-item svg { width: 18px; height: 18px; margin-right: 18px; fill: var(--brand-blue); flex: none; }

  .divider { position: absolute; left: 258px; top: 267px; width: 1px; height: 110px; background: var(--rule); }

  .address {
    position: absolute; left: 284px; top: 303px;
    color: var(--ink); font-size: 18px; line-height: 27px; font-style: normal;
  }
  .web { letter-spacing: 3px; }

  .band {
    position: absolute; left: 0; bottom: 0; width: 100%; height: 17px;
    background: linear-gradient(90deg, #16375c, var(--brand-blue) 45%, #1d4a7c);
  }

  .back-web {
    position: absolute; left: 0; top: 358px; width: 100%; text-align: center;
    color: var(--ink-soft); font-size: 18px; letter-spacing: 3.5px;
  }
</style>
</head>
<body>
<main class="canvas">
  <section class="card card--front">
    <div class="brand-name">Brindle<br>Sky Port</div>

    <div class="holder">
      <div class="holder-name">Dana Reyes</div>
      <div class="holder-title">President</div>
    </div>

    <ul class="contact-list">
      <li class="contact-item">
        <svg viewBox="0 0 24 24"><path d="M3 8c0-3 4-5 9-5s9 2 9 5v2h-5V8H8v2H3zM6 11h12l2 9H4z"/></svg>
        555 0142 7781
      </li>
      <li class="contact-item">
        <svg viewBox="0 0 24 24"><path d="M7 1h10a2 2 0 0 1 2 2v18a2 2 0 0 1-2 2H7a2 2 0 0 1-2-2V3a2 2 0 0 1 2-2zm0 3v14h10V4zm5 15.5a1 1 0 1 0 0 2 1 1 0 0 0 0-2z"/></svg>
        555 0198 3346
      </li>
      <li class="contact-item">
        <svg viewBox="0 0 24 24"><path d="M6 2h10l2 2v5H6zM3 10h18v9H3zm3 6v6h12v-6z"/></svg>
        555 0173 6620
      </li>
      <li class="contact-item">
        <svg viewBox="0 0 24 24"><path d="M2 5h20v14H2zm2 2v1l8 5 8-5V7l-8 5z"/></svg>
        dana@bspjets.com
      </li>
    </ul>

    <div class="divider"></div>

    <address class="address">
      4127 Runway Crest Lane<br>
      Cedar Hollow, NY 10990<br>
      <span class="web">www.bspjets.com</span>
    </address>

    <div class="band"></div>
  </section>

  <section class="card card--back">
    <div class="brand-name">Brindle<br>Sky Port</div>
    <div class="back-web">www.bspjets.com</div>
  </section>
</main>
</body>
</html>
```